Design a "healthy, happy dog and cat" cheque/check background

I am looking for a few design concepts featuring a happy healthy dog and cat, that will be used as the background of a paper cheque/check.

This will require Photoshop and stock photos.

Here is the design brief: https://docs.plinvaro.com/document/d/4Rt8mKx2LqW9zVbN3cHy7TfJ1sDp6GaE0uYoZiXeMwnB/edit?usp=sharing

Colors

Designer to choose colors to be used in the design.

Requirements
Must have
• A happy dog and cat the main focus within the "empty" central part of the cheque/check, and a complementary background for the rest of the cheque, following the design guidelines in the attached plinvaro doc.

```html
<!DOCTYPE html>
<html lang="en">
<head>
<meta charset="utf-8">
<title>Quickleaf Personal Cheque – Dog and Cat</title>
<link href="https://fonts.googleapis.com/css2?family=Arimo:wght@400;700&family=Cousine:wght@700&display=swap" rel="stylesheet">
<style>
  :root {
    --stage: #000000;
    --paper: #ffffff;
    --field-start: #eef1b2;
    --field-mid: #f4dfa0;
    --field-end: #f3a65e;
    --ink: #2f2f2f;
    --ink-soft: #3b3b3b;
    --ink-dark: #1e1e1e;
    --rule: #3a3a3a;
    --pet-cream: #f3ede0;
    --pet-tan: #e6cfa4;
    --micr: #111111;
  }
  * { margin: 0; padding: 0; box-sizing: border-box; }
  html, body { width: 1200px; height: 1000px; overflow: hidden; background: var(--stage); }
  body { position: relative; font-family: "Arimo", Arial, sans-serif; color: var(--ink); }

  .cheque-sheet { position: absolute; left: 15px; top: 215px; width: 1170px; height: 531px; background: var(--paper); }
  .cheque-field {
    position: absolute; left: 38px; top: 237px; width: 1147px; height: 385px;
    background: linear-gradient(90deg, var(--field-start) 0%, var(--field-mid) 45%, var(--field-end) 80%, var(--field-end) 100%);
  }
  .pet-photo {
    position: absolute; left: 40px; top: 264px; width: 826px; height: 358px;
    border-radius: 40px 40px 0 0;
    background: linear-gradient(90deg, var(--pet-cream) 0%, var(--pet-tan) 45%, var(--pet-cream) 100%);
    opacity: 0.85;
  }

  .abs { position: absolute; white-space: nowrap; }
  .account-name { left: 71px; top: 276px; font-size: 21px; font-weight: 700; color: var(--ink-soft); }
  .account-address { left: 72px; top: 299px; font-size: 19px; line-height: 22px; color: var(--ink-soft); }
  .cheque-number { left: 1013px; top: 262px; font-size: 22px; font-weight: 700; color: #111; }

  .date-label { left: 779px; top: 323px; font-size: 18px; color: var(--ink-soft); }
  .date-boxes { left: 843px; top: 305px; display: flex; gap: 3px; }
  .date-box { width: 35px; height: 35px; background: var(--paper); }
  .date-format { left: 843px; top: 344px; display: flex; gap: 3px; font-size: 13px; color: var(--ink-soft); }
  .date-format span { width: 35px; text-align: center; }

  .payee-label { left: 70px; top: 402px; font-size: 14px; line-height: 14px; color: var(--ink-soft); }
  .dollar-sign { left: 940px; top: 398px; font-size: 30px; color: var(--ink-soft); }
  .amount-box { left: 963px; top: 387px; width: 189px; height: 46px; background: var(--paper); }
  .dollars-label { left: 911px; top: 463px; font-size: 14px; color: var(--ink-soft); }

  .bank-mark { left: 84px; top: 508px; width: 60px; height: 60px; border-radius: 50%; background: var(--ink-dark); }
  .bank-name { left: 165px; top: 507px; font-size: 20px; font-weight: 700; letter-spacing: 0.8px; color: var(--ink-dark); }
  .bank-address { left: 165px; top: 527px; font-size: 19px; line-height: 19px; letter-spacing: 1.5px; color: var(--ink-dark); }
  .company-line { left: 804px; top: 541px; font-size: 14px; color: var(--ink-dark); }
  .memo-label { left: 75px; top: 590px; font-size: 12px; color: var(--ink-soft); }

  .security-badge { left: 1147px; top: 482px; width: 30px; height: 130px; border: 1px dashed #555; }
  .security-text { left: 1150px; top: 553px; transform: rotate(-90deg); transform-origin: left top; font-size: 8px; line-height: 9px; color: #333; }
  .security-lock { left: 1154px; top: 556px; width: 16px; height: 24px; }
  .security-square { left: 1153px; top: 596px; width: 18px; height: 12px; background: #333; }

  .rules { position: absolute; left: 0; top: 0; width: 1200px; height: 1000px; }

  .micr-line { left: 66px; top: 652px; font-family: "Cousine", monospace; font-weight: 700; font-size: 30px; letter-spacing: 6px; color: var(--micr); }
</style>
</head>
<body>
  <div class="cheque-sheet"></div>
  <div class="cheque-field"></div>

  <div class="pet-photo" role="img" aria-label="Photo of a happy cocker spaniel puppy cuddling a fluffy white kitten, lying across the centre of the cheque"></div>

  <svg class="rules" viewBox="0 0 1200 1000" aria-hidden="true">
    <g stroke="var(--rule)" stroke-width="1.5" fill="none">
      <path d="M70 432 H915 V405"/>
      <path d="M72 485 H898 L905 455"/>
      <path d="M70 604 H587"/>
      <path d="M683 604 H1087"/>
    </g>
  </svg>

  <div class="abs account-name">NCPR - Quickleaf Cheques Personal Cheque</div>
  <div class="abs account-address">42 Maplewood Lane<br>Kingsbridge, Ontario K2P 4R8</div>
  <div class="abs cheque-number">101</div>

  <div class="abs date-label">DATE</div>
  <div class="abs date-boxes">
    <div class="date-box"></div><div class="date-box"></div><div class="date-box"></div><div class="date-box"></div>
    <div class="date-box"></div><div class="date-box"></div><div class="date-box"></div><div class="date-box"></div>
  </div>
  <div class="abs date-format"><span>D</span><span>D</span><span>M</span><span>M</span><span>Y</span><span>Y</span><span>Y</span><span>Y</span></div>

  <div class="abs payee-label">PAY TO THE<br>ORDER OF</div>
  <div class="abs dollar-sign">$</div>
  <div class="abs amount-box"></div>
  <div class="abs dollars-label">100 DOLLARS</div>

  <div class="abs bank-mark" aria-hidden="true"></div>
  <div class="abs bank-name">Your Financial Institution</div>
  <div class="abs bank-address">310 Ledger Avenue<br>Your City, Your Province A1B 2CS</div>
  <div class="abs company-line">Optional Company Name</div>
  <div class="abs memo-label">MEMO</div>

  <div class="abs security-badge"></div>
  <div class="abs security-text">Details on Back<br>Details au Verso</div>
  <svg class="abs security-lock" viewBox="0 0 16 24" aria-hidden="true">
    <path d="M4 10 V6 a4 4 0 0 1 8 0 V10" stroke="#333" stroke-width="1.5" fill="none"/>
    <rect x="1.5" y="10" width="13" height="12" fill="none" stroke="#333" stroke-width="1.5"/>
  </svg>
  <div class="abs security-square"></div>

  <div class="abs micr-line">⑈101⑈ ⑆12345⑉678⑆ 12345⑉6789⑈</div>
</body>
</html>
```